Shop Window Desgin

I have a big glass window (office), 280cm wide by 302cm high and I want designing an advert for our property management business.

Our main colours are in the proeprty management logo attached. I have also uploaded a photo of the shop front (left window), please take into consideration the door.

I want the following text items placed:

PROPERTY MANAGEMENT
HOLIDAY RENTALS
KEYHOLDING
MARKETING & RESERVATIONS
GARDEN & POOL MAINTENACE
CLEANING & LAUNDRY

```html
<!DOCTYPE html>
<html lang="en">
<head>
<meta charset="utf-8">
<title>Harbourline Property Management – Window Advert</title>
<link href="https://fonts.googleapis.com/css2?family=Montserrat:wght@500;700;800&family=Questrial&family=Open+Sans:ital,wght@1,400&display=swap" rel="stylesheet">
<style>
  :root {
    --orange: #e8802a;
    --white: #ffffff;
    --grey: #6b6b6b;
    --grey-icon: #777777;
    --grey-line: #9a9a9a;
    --badge-grey: #d9d6e0;
    --badge-blue: #1d8fd8;
  }
  * { box-sizing: border-box; margin: 0; padding: 0; }
  html, body { width: 1118px; height: 1200px; overflow: hidden; background: var(--white); }
  .advert {
    position: relative;
    width: 1118px;
    height: 1200px;
    overflow: hidden;
    background: var(--orange);
    font-family: "Questrial", sans-serif;
  }
  .skyline-area {
    position: absolute;
    left: 70px; top: 70px;
    width: 978px; height: 470px;
    border-radius: 24px;
    background: linear-gradient(180deg, rgba(255,255,255,0.18) 0%, rgba(255,255,255,0.45) 60%, rgba(255,255,255,0.7) 100%);
  }
  .dome {
    position: absolute;
    left: 0; top: 0;
    width: 1118px; height: 1200px;
  }
  .brand-plate {
    position: absolute;
    left: 316px; top: 437px;
    width: 462px; height: 144px;
    background: var(--white);
    border: 6px solid var(--orange);
    border-radius: 34px;
    display: flex;
    flex-direction: column;
    align-items: center;
    justify-content: center;
    color: var(--orange);
    font-family: "Montserrat", sans-serif;
    font-weight: 800;
    text-transform: uppercase;
    line-height: 1;
  }
  .brand-name { font-size: 50px; letter-spacing: 1px; }
  .brand-sub { font-size: 21px; margin-top: 8px; letter-spacing: 0.5px; }
  .services {
    position: absolute;
    left: 0; top: 642px;
    width: 1118px;
    list-style: none;
  }
  .service {
    position: absolute;
    top: 0;
    width: 170px;
    margin-left: -85px;
    text-align: center;
    color: var(--grey);
    font-size: 19px;
    line-height: 1.1;
    text-transform: uppercase;
  }
  .service-icon { display: block; width: 112px; height: 112px; margin: 0 auto 18px; }
  .service-icon circle.disc { fill: var(--grey-icon); }
  .service-icon .glyph { fill: none; stroke: var(--white); stroke-width: 4; stroke-linecap: round; stroke-linejoin: round; }
  .about {
    position: absolute;
    left: 182px; top: 845px;
    width: 754px;
    text-align: center;
    font-family: "Open Sans", sans-serif;
    font-style: italic;
    font-size: 13px;
    line-height: 1.45;
    color: var(--grey);
  }
  .divider {
    position: absolute;
    left: 89px; top: 975px;
    width: 940px; height: 2px;
    background: var(--grey-line);
  }
  .contact { position: absolute; left: 89px; top: 993px; font-family: "Montserrat", sans-serif; }
  .contact-label { font-size: 25px; font-weight: 500; color: var(--grey); letter-spacing: 0.5px; }
  .contact-phone { font-size: 44px; font-weight: 700; color: var(--orange); line-height: 1.2; }
  .badge-assoc {
    position: absolute;
    left: 644px; top: 1016px;
    width: 176px; height: 60px;
    border-radius: 8px;
    background: var(--badge-grey);
  }
  .badge-cert {
    position: absolute;
    left: 890px; top: 1000px;
    width: 122px; height: 100px;
    border-radius: 34px;
    background: var(--badge-blue);
  }
  .footer-band {
    position: absolute;
    left: 0; bottom: 0;
    width: 1118px; height: 56px;
    background: var(--orange);
  }
</style>
</head>
<body>
<main class="advert">
  <div class="skyline-area" role="img" aria-label="City skyline illustration of tall white apartment towers"></div>

  <svg class="dome" viewBox="0 0 1118 1200" aria-hidden="true">
    <path d="M0 600 Q559 330 1118 600 L1118 1200 L0 1200 Z" fill="#ffffff"/>
  </svg>

  <div class="brand-plate">
    <span class="brand-name">Harbourline</span>
    <span class="brand-sub">Property Management</span>
  </div>

  <ul class="services">
    <li class="service" style="left:160px">
      <svg class="service-icon" viewBox="0 0 112 112" aria-hidden="true">
        <circle class="disc" cx="56" cy="56" r="56"/>
        <rect class="glyph" x="26" y="52" width="34" height="28" rx="3"/>
        <circle class="glyph" cx="40" cy="38" r="10"/>
        <path class="glyph" d="M66 54h20M66 64h20M66 74h20"/>
      </svg>
      Property<br>Management
    </li>
    <li class="service" style="left:320px">
      <svg class="service-icon" viewBox="0 0 112 112" aria-hidden="true">
        <circle class="disc" cx="56" cy="56" r="56"/>
        <circle class="glyph" cx="68" cy="42" r="16"/>
        <circle class="glyph" cx="72" cy="38" r="4"/>
        <path class="glyph" d="M56 54 L28 82 M34 76 l6 6 M40 70 l6 6"/>
      </svg>
      Keyholding
    </li>
    <li class="service" style="left:480px">
      <svg class="service-icon" viewBox="0 0 112 112" aria-hidden="true">
        <circle class="disc" cx="56" cy="56" r="56"/>
        <path class="glyph" d="M40 52 L58 36 L76 52 M44 48 V66 H72 V48"/>
        <path class="glyph" d="M24 74 Q40 70 52 78 H70 Q80 78 88 70"/>
      </svg>
      Holiday<br>Rentals
    </li>
    <li class="service" style="left:640px">
      <svg class="service-icon" viewBox="0 0 112 112" aria-hidden="true">
        <circle class="disc" cx="56" cy="56" r="56"/>
        <rect class="glyph" x="26" y="32" width="28" height="46" rx="2"/>
        <circle class="glyph" cx="74" cy="40" r="12"/>
        <path class="glyph" d="M68 40 l4 4 l8 -8 M60 70 h24 v12 h-24 z"/>
      </svg>
      Marketing &amp;<br>Reservations
    </li>
    <li class="service" style="left:800px">
      <svg class="service-icon" viewBox="0 0 112 112" aria-hidden="true">
        <circle class="disc" cx="56" cy="56" r="56"/>
        <path class="glyph" d="M44 64 V36 Q44 28 52 28 M66 64 V36 Q66 28 74 28 M44 44 H66 M44 54 H66"/>
        <path class="glyph" d="M28 72 q7 -5 14 0 t14 0 t14 0 t14 0 M28 82 q7 -5 14 0 t14 0 t14 0 t14 0"/>
      </svg>
      Garden &amp; Pool<br>Maintenace
    </li>
    <li class="service" style="left:960px">
      <svg class="service-icon" viewBox="0 0 112 112" aria-hidden="true">
        <circle class="disc" cx="56" cy="56" r="56"/>
        <path class="glyph" d="M20 34 Q56 44 92 34"/>
        <path class="glyph" d="M46 40 L32 48 L38 58 L42 56 V82 H70 V56 L74 58 L80 48 L66 40 Q56 48 46 40 Z"/>
      </svg>
      Cleaning &amp;<br>Laundry
    </li>
  </ul>

  <p class="about">Harbourline Property Management advances the professionally-managed vacation and holiday rental industry by providing education, information, and networking opportunities, promoting the value of the vacation rental experience, and speaking as the authoritative voice to foster professionalism, collaboration, and growth.</p>

  <div class="divider"></div>

  <div class="contact">
    <p class="contact-label">CALL US</p>
    <p class="contact-phone">+1 555 010 2040</p>
  </div>

  <div class="badge-assoc" role="img" aria-label="Rental association membership badge"></div>
  <div class="badge-cert" role="img" aria-label="Pool and spa operator certification badge"></div>

  <div class="footer-band"></div>
</main>
</body>
</html>
```